plumbers buisness card

A buisness card for a plumbing buisness
needs to have a water theme with navy blue, light blue and white
with an image of either a water drop, pipes, tools or something relating to plumbing and incorperating my buisness name as a logo

"Kettering Plumbing" is the words that need to stand out with "& gasfitting" to be smaller

spelling error on brief, "maintenance"
and also could you include my email d_kettering@mailwave.com.au

Industry/Entity Type

Plumbing

Contact Information for Business Card

Kettering Plumbing & Gasfitting

declan kettering
0432961085

specialising in
-new homes
-maitenance
-renovations

license no.
-73840

```html
<!DOCTYPE html>
<html lang="en">
<head>
<meta charset="utf-8">
<title>Kettering Plumbing – Business Card</title>
<link rel="stylesheet" href="https://fonts.googleapis.com/css2?family=Source+Sans+3:wght@400;600;700&family=Arimo&display=swap">
<style>
  :root {
    --sheet: #fff673;
    --label: #1a1a1a;
    --ink: #ffffff;
    --navy-deep: #26167e;
    --navy: #2d1c86;
    --charcoal: #1b1b22;
    --brass-dark: #6e5418;
    --brass: #c9a43a;
    --brass-glow: #f1dc8c;
    --olive-grey: #9b8f7c;
    --olive: #878443;
    --sage: #8f9a7e;
  }
  * { margin: 0; padding: 0; box-sizing: border-box; }
  html, body {
    width: 1200px; height: 431px; overflow: hidden;
    background: var(--sheet);
  }
  .sheet {
    position: relative; width: 1200px; height: 431px;
    font-family: "Source Sans 3", "Myriad Pro", sans-serif;
    color: var(--ink);
  }
  .side-label {
    position: absolute;
    font-family: "Arimo", Arial, sans-serif;
    font-size: 29px; font-weight: 400; color: var(--label);
    transform: translateX(-50%);
  }
  .side-label--front { left: 290px; top: 22px; }
  .side-label--back { left: 877px; top: 15px; }

  .card {
    position: absolute; top: 81px;
    width: 544px; height: 310px; overflow: hidden;
  }
  .card--front { left: 27px; }
  .card--back { left: 611px; }

  .card__ground { position: absolute; inset: 0; }
  .card--front .card__ground {
    background:
      radial-gradient(ellipse 380px 300px at 0% 100%, #2a3ba8 0%, transparent 70%),
      linear-gradient(90deg, var(--navy) 0%, var(--navy-deep) 50%, var(--charcoal) 100%);
  }
  .card--back .card__ground {
    background:
      radial-gradient(ellipse 200px 120px at 0% 100%, var(--sage), transparent 70%),
      linear-gradient(90deg, var(--olive-grey) 0%, #938b6c 55%, var(--olive) 100%);
  }

  /* area reserved for the brass tap photograph */
  .card__photo {
    position: absolute; left: 0; top: 8px;
    width: 390px; height: 210px;
    border-radius: 0 60% 45% 0 / 0 55% 60% 0;
    background:
      radial-gradient(ellipse 150px 70px at 180px 40px, var(--brass-glow), transparent 80%),
      linear-gradient(150deg, var(--brass) 0%, var(--brass-glow) 35%, var(--brass) 60%, var(--brass-dark) 100%);
    opacity: .85;
  }
  .card--back .card__photo { opacity: .7; }

  .card__text { position: absolute; white-space: nowrap; }
  .brand-name { font-weight: 700; font-size: 27px; }
  .brand-trade { font-size: 22px; transform: translateX(-50%); }
  .contact-name { font-weight: 700; transform: translateX(-50%); }
  .contact-phone { font-weight: 700; transform: translateX(-50%); }

  .card--front .brand-name { right: 24px; top: 43px; }
  .card--front .brand-trade { left: 403px; top: 78px; }
  .card--front .contact-name { left: 420px; top: 146px; font-size: 17px; }
  .card--front .contact-phone { left: 420px; top: 168px; font-size: 15px; letter-spacing: .4px; }

  .services {
    left: 277px; top: 238px; font-size: 16.5px;
    transform: translateX(-50%);
  }
  .services__lead { font-weight: 700; }
  .email { left: 277px; top: 259px; font-size: 16px; transform: translateX(-50%); }
  .divider {
    position: absolute; left: 80px; top: 281px;
    width: 401px; height: 1px; background: var(--ink); opacity: .85;
  }
  .license {
    left: 277px; top: 286px; font-size: 14px; font-weight: 700;
    transform: translateX(-50%);
  }

  .card--back .brand-name { right: 31px; top: 40px; }
  .card--back .brand-trade { left: 397px; top: 76px; }
  .card--back .contact-name { left: 127px; top: 218px; font-size: 24px; }
  .card--back .contact-phone { left: 127px; top: 251px; font-size: 23px; }
</style>
</head>
<body>
<main class="sheet">
  <h2 class="side-label side-label--front">Front</h2>
  <h2 class="side-label side-label--back">Back</h2>

  <section class="card card--front">
    <div class="card__ground"></div>
    <div class="card__photo" role="img" aria-label="Photograph of a curved brass tap spout arching across the card"></div>
    <h1 class="card__text brand-name">Kettering Plumbing</h1>
    <p class="card__text brand-trade">&amp; gasfitting</p>
    <p class="card__text contact-name">Declan Kettering</p>
    <p class="card__text contact-phone">0432961085</p>
    <p class="card__text services"><span class="services__lead">Specialising in -</span> New homes - Maintenance - Renovations</p>
    <p class="card__text email">email : d_kettering@mailwave.com.au</p>
    <div class="divider"></div>
    <p class="card__text license">license no. -73840</p>
  </section>

  <section class="card card--back">
    <div class="card__ground"></div>
    <div class="card__photo" role="img" aria-label="Photograph of a curved brass tap spout on a soft olive background"></div>
    <h1 class="card__text brand-name">Kettering Plumbing</h1>
    <p class="card__text brand-trade">&amp; gasfitting</p>
    <p class="card__text contact-name">Declan Kettering</p>
    <p class="card__text contact-phone">0432961085</p>
  </section>
</main>
</body>
</html>
```